Webdesign für Hersteller für Pack- und Palettieranlagen für den Getränke- und Lebensmittelbereich
Webdesign für Hersteller für Pack- und Palettieranlagen für den Getränke- und Lebensmittelbere..
Zielgruppe
Hersteller für Pack- und Palettieranlagen für den Getränke- und Lebensmittelbereich
Zielgruppe: Getränke- und Lebensmittelhersteller
Aufgabenstellung
die zukünftige Seite soll dynamischer und intuitiver werden
klare Strukturen, aber morderner als das jetztige Layout
Keine Kopie der alten Seite www.kolmatech.de!
Startseite soll aufgeräumter sein
Logo, Rufnummer, Mail, Social Media
Startseite mit großem Headerbild (Slider)

```html
<!DOCTYPE html>
<html lang="de">
<head>
<meta charset="utf-8">
<title>Kolmatech Maschinenbau – Pack- und Palettieranlagen</title>
<link href="https://fonts.googleapis.com/css2?family=Inter:wght@400;500;600;700;800;900&display=swap" rel="stylesheet">
<style>
:root{
  --green:#6ab42d;
  --green-dark:#4f8f1c;
  --orange:#f07f1e;
  --ink:#2b2b2b;
  --muted:#777;
  --light:#f2f2f2;
  --field:#ececec;
  --footer:#3b3b3b;
  --white:#fff;
}
*{box-sizing:border-box;margin:0;padding:0}
html,body{width:1200px;height:3196px;overflow:hidden}
body{font-family:'Inter',sans-serif;color:var(--ink);background:var(--white);position:relative}
.topbar{position:absolute;left:0;top:0;width:1200px;height:37px;background:var(--green);color:#fff;font-size:13px;display:flex;align-items:center;padding:0 80px}
.topbar .item{display:flex;align-items:center;gap:8px;margin-right:38px}
.topbar .social{margin-left:auto;display:flex;gap:10px}
.topbar .social span{width:14px;height:14px;border-radius:50%;background:#fff;display:block}
.nav{position:absolute;left:0;top:37px;width:1200px;height:57px;background:#fff;display:flex;align-items:center;padding:0 78px}
.brand{display:flex;align-items:center;gap:6px;font-weight:900;font-size:17px;color:var(--green);line-height:1;white-space:nowrap}
.brand .dot{width:16px;height:16px;border-radius:50%;background:var(--green)}
.brand small{display:block;font-size:7px;font-weight:900;color:var(--green);margin-top:2px}
.nav ul{list-style:none;display:flex;gap:17px;margin-left:auto;font-size:11px;font-weight:600;color:#333;letter-spacing:.1px;white-space:nowrap}
.hero{position:absolute;left:0;top:94px;width:1200px;height:499px;background:linear-gradient(100deg,#2f2f2f 0%,#4a4a45 40%,#5d6b45 65%,#6f8f3a 85%,#4b5a36 100%)}
.hero .content{position:absolute;left:78px;top:95px;color:#fff}
.hero h1{font-size:43px;font-weight:800;line-height:1.02;letter-spacing:-.3px;white-space:nowrap}
.hero p{font-size:11px;font-weight:600;line-height:1.05;width:410px;margin-top:20px}
.btn{display:inline-flex;align-items:center;justify-content:center;font-weight:700;font-size:13px;height:37px;padding:0 20px}
.btn-green{background:var(--green);color:#fff}
.btn-ghost{border:2px solid #fff;color:#fff}
.hero .actions{display:flex;gap:25px;margin-top:27px}
.dots{position:absolute;left:569px;top:470px;display:flex;gap:9px}
.dots span{width:8px;height:8px;background:#fff}
.dots span:first-child{background:transparent;border:2px solid #fff}
.section-title{position:absolute;left:0;width:1200px;text-align:center;font-size:25px;font-weight:800;color:#444}
.section-title span{display:inline-block;padding:0 16px 6px;border-bottom:2px solid var(--green)}
.products{position:absolute;left:0;top:593px;width:1200px;height:499px;background:var(--light)}
.pcard{position:absolute;top:125px;width:238px;height:300px;background:#fff;text-align:center;box-shadow:0 6px 18px rgba(0,0,0,.06)}
.pcard .img{height:175px}
.pcard h3{font-size:12.5px;font-weight:700;margin-top:15px;letter-spacing:.2px}
.pcard p{font-size:8.5px;color:var(--muted);margin-top:7px;line-height:1.2}
.pcard .more{display:inline-flex;align-items:center;justify-content:center;width:150px;height:35px;border:2px solid #333;font-size:12.5px;font-weight:700;margin-top:13px}
.pcard.active{background:var(--green);color:#fff}
.pcard.active p{color:#eaf5df}
.pcard.active .more{border-color:#fff}
.news{position:absolute;left:0;top:1092px;width:1200px;height:465px;background:#fff;overflow:hidden}
.ncard{position:absolute;top:122px;width:282px;height:268px;background:#fff;box-shadow:0 4px 16px rgba(0,0,0,.1)}
.ncard .img{height:95px;background:linear-gradient(180deg,#9a3a1c,#c76a25 50%,#8b8f95)}
.ncard .body{padding:18px 18px 0}
.ncard .date{font-size:8px;color:var(--muted)}
.ncard h4{font-size:12.5px;font-weight:700;margin-top:14px;white-space:nowrap}
.ncard p{font-size:8.6px;line-height:1.08;color:var(--muted);margin-top:10px}
.ncard .read{display:flex;justify-content:space-between;font-size:9.5px;font-weight:700;color:var(--orange);margin-top:26px}
.ncard.active{background:var(--orange);color:#fff}
.ncard.active .date,.ncard.active p,.ncard.active .read{color:#fff}
.jobs{position:absolute;left:0;top:1557px;width:1200px;height:364px;background:var(--green)}
.jobs .section-title{color:#fff;top:40px}
.jobs .section-title span{border-color:#fff}
.person{position:absolute;left:0;top:25px;width:250px;height:339px;background:linear-gradient(180deg,#e9e9e6 0%,#cfd3d6 40%,#8d9aa8 100%);border-radius:120px 120px 0 0}
.jcard{position:absolute;top:125px;width:282px;height:167px;background:#fff;padding:14px 14px 0 20px}
.jcard .date{font-size:8px;color:var(--muted)}
.jcard h4{font-size:12.5px;font-weight:700;margin-top:12px}
.jcard p{font-size:8.6px;line-height:1.08;color:var(--muted);margin-top:10px}
.jcard .apply{display:flex;width:144px;height:35px;margin:14px auto 0;align-items:center;justify-content:center;background:var(--green);color:#fff;font-size:12.5px;font-weight:700}
.jcard .apply.orange{background:var(--orange)}
.company{position:absolute;left:0;top:1921px;width:1200px;height:573px;background:linear-gradient(180deg,#fff 0%,#fff 55%,#e6e6e6 80%,#d2d2d2 100%);overflow:hidden}
.company .section-title{top:40px}
.timeline{position:absolute;left:0;top:114px;width:1200px;height:1px;border-top:1px dashed var(--green)}
.pin{position:absolute;top:104px;width:22px;height:45px}
.tcard{position:absolute;top:149px;width:200px;height:99px;background:#fff;box-shadow:0 3px 10px rgba(0,0,0,.12);padding:16px 15px}
.tcard .year{font-size:9.5px;font-weight:700;color:var(--green)}
.tcard h5{font-size:13.5px;font-weight:700;margin-top:12px;line-height:1.05;color:#333}
.company .logo{position:absolute;left:160px;top:312px;display:flex;align-items:center;gap:10px}
.company .logo .dot{width:36px;height:36px;border-radius:50%;background:var(--green);flex:none}
.company .logo .name{font-size:38px;font-weight:900;color:var(--green);line-height:1;white-space:nowrap}
.company .logo .sub{font-size:17px;font-weight:700;color:#222;margin-top:5px;text-align:right;white-space:nowrap}
.company .text{position:absolute;left:527px;top:293px;width:535px;font-size:10.4px;line-height:1.08;color:#444}
.company .text p{margin-bottom:10px}
.btn-dark{position:absolute;left:527px;top:462px;width:143px;height:36px;background:#4a4a4a;color:#fff;font-weight:700;font-size:12.5px;display:flex;align-items:center;justify-content:center}
.contact{position:absolute;left:0;top:2494px;width:1200px;height:474px;background:#fff}
.contact .section-title{top:44px}
.form{position:absolute;left:114px;top:135px;width:384px}
.form .row{display:flex;gap:34px;margin-bottom:20px}
.form label{display:block;font-size:11px;margin-bottom:4px;color:#333}
.form .field{width:175px;height:25px;background:var(--field);font-size:11px;color:#aaa;padding:6px 8px}
.form .field.filled{color:#333}
.form .area{width:384px;height:81px;background:var(--field);font-size:11px;color:#aaa;padding:9px 8px;margin-top:10px}
.send{position:absolute;left:0;top:228px;width:144px;height:37px;background:var(--orange);color:#fff;font-weight:600;font-size:13px;display:flex;align-items:center;justify-content:center;gap:12px}
.building{position:absolute;left:527px;top:131px;width:673px;height:343px;background:linear-gradient(180deg,#d7dde3 0%,#aab4bd 45%,#5b6670 70%,#8b8f91 100%)}
.footer{position:absolute;left:0;top:2968px;width:1200px;height:228px;background:var(--footer);color:#fff}
.footer h6{font-size:11px;font-weight:700;letter-spacing:.3px}
.fcol{position:absolute;top:52px;font-size:9px;line-height:1.35}
.fcol .links{display:grid;gap:8px 18px;margin-top:14px}
.footer .copy{position:absolute;left:0;top:184px;width:1200px;border-top:1px solid #555;text-align:center;padding-top:14px;font-size:9px;font-weight:600}
.newsletter{position:absolute;left:952px;top:56px}
.newsletter .lbl{font-size:8.5px}
.newsletter .box{display:flex;margin-top:10px}
.newsletter .in{width:123px;height:25px;background:#fff;color:#777;font-size:8px;padding:8px}
.newsletter .go{width:31px;height:25px;background:var(--green);display:flex;align-items:center;justify-content:center}
</style>
</head>
<body>

<header>
  <div class="topbar">
    <div class="item">
      <svg width="12" height="12" viewBox="0 0 24 24"><path fill="#fff" d="M6.6 10.8a15 15 0 0 0 6.6 6.6l2.2-2.2c.3-.3.7-.4 1-.2 1.1.4 2.3.6 3.6.6.6 0 1 .4 1 1V20c0 .6-.4 1-1 1A17 17 0 0 1 3 4c0-.6.4-1 1-1h3.5c.6 0 1 .4 1 1 0 1.3.2 2.5.6 3.6.1.3 0 .7-.2 1z"/></svg>
      03541 / 720 - 0
    </div>
    <div class="item">
      <svg width="14" height="11" viewBox="0 0 24 18"><rect x="1" y="1" width="22" height="16" rx="2" fill="#fff"/><path d="M2 2l10 8 10-8" stroke="#6ab42d" stroke-width="2" fill="none"/></svg>
      info@kolmatech.de
    </div>
    <div class="social"><span></span><span></span><span></span><span></span></div>
  </div>
  <nav class="nav">
    <div class="brand"><span class="dot"></span><div>KOLMATECH<small>Maschinenbau GmbH</small></div></div>
    <ul>
      <li>UNTERNEHMEN</li><li>JOBS / KARRIERE</li><li>PALETTIERTECHNIK</li><li>PACKERTECHNIK</li><li>FÖRDERTECHNIK</li><li>ANLAGEN</li><li>GEBRAUCHTMASCHINEN</li><li>AKTUELLES</li>
    </ul>
  </nav>
</header>

<section class="hero" role="img" aria-label="Abfüllanlage mit Förderbändern voller grüner Flaschen">
  <div class="content">
    <h1>Hersteller Für Pack-<br>Und Palettieranlagen<br>Für Den Getränke-<br>Und Lebensmittelbereich</h1>
    <p>Lorem Ipsum Dolor Sit Amet, Consectetur Adipiscing Elit, Sed Do Eiusmod Tempor Incididunt Ut Labore Et Dolore Magna Aliqua. Ut Enim Ad Minim Veniam, Quis Nostrud Exercitation Ullamco Laboris Nisi Ut Aliquip Ex Ea Commodo Consequat.</p>
    <div class="actions"><span class="btn btn-green">Unsere Produkte</span><span class="btn btn-ghost">Mehr Erfahren</span></div>
  </div>
  <div class="dots"><span></span><span></span><span></span><span></span></div>
</section>

<section class="products">
  <h2 class="section-title" style="top:40px"><span>PRODUKTE</span></h2>
  <div class="pcard" style="left:77px"><div class="img" role="img" aria-label="Palettieranlage in einer Werkshalle" style="background:linear-gradient(160deg,#b9bcc0,#d7c13a 55%,#7b7f84)"></div><h3>PALETTIERTECHNIK</h3><p>KoPal<br>Unsere Palettierfamilie</p><span class="more">Mehr Erfahren</span></div>
  <div class="pcard active" style="left:346px"><div class="img" role="img" aria-label="Flaschenpacker mit gelben Kästen" style="background:linear-gradient(180deg,#c5c9cc,#9ea3a6 45%,#e0c02a 75%,#8a8d8f)"></div><h3>PACKERTECHNIK</h3><p>KoPac<br>Unsere Flaschenpacker</p><span class="more">Mehr Erfahren</span></div>
  <div class="pcard" style="left:615px"><div class="img" role="img" aria-label="Förderband mit braunen Flaschen" style="background:linear-gradient(180deg,#d8dadb,#9c9b97 40%,#6b4326 70%,#b13a2d)"></div><h3>FÖRDERTECHNIK</h3><p>KoTrans<br>Behälter- Und Gebindetransport</p><span class="more">Mehr Erfahren</span></div>
  <div class="pcard" style="left:884px"><div class="img" role="img" aria-label="Gebrauchte Anlage vor Holzfässern" style="background:linear-gradient(160deg,#c9ccd0,#9a8a74 50%,#3a3a3a)"></div><h3>GEBRAUCHTMASCHINEN</h3><p>KoPal<br>Unsere Palettierfamilie</p><span class="more">Mehr Erfahren</span></div>
</section>

<section class="news">
  <h2 class="section-title" style="top:40px"><span>AKTUELLES</span></h2>
  <article class="ncard" style="left:77px"><div class="img" role="img" aria-label="Braune Glasflaschen auf einer Abfüllanlage"></div><div class="body"><div class="date">März 14, 2024</div><h4>Neue Abfüllanlage für Brunnhof Limo</h4><p>Der Traditionsreiche Limonadenhersteller Brunnhof Limo Aus Der Oberlausitz Investierte 2022/23 In Eine Neue Abfüllanlage. Federführend Beteiligt Bei Planung, Schnittstellenklärung Und Lieferung Der Anlage War Unser Unternehmen, In Zusammenarbeit Mit Weiteren Mittelständigen Firmen.</p><div class="read"><span>Weiter Lesen</span><span>→</span></div></div></article>
  <article class="ncard active" style="left:390px"><div class="img" role="img" aria-label="Braune Glasflaschen auf einer Abfüllanlage"></div><div class="body"><div class="date">März 14, 2024</div><h4>Neue Abfüllanlage für Brunnhof Limo</h4><p>Der Traditionsreiche Limonadenhersteller Brunnhof Limo Aus Der Oberlausitz Investierte 2022/23 In Eine Neue Abfüllanlage. Federführend Beteiligt Bei Planung, Schnittstellenklärung Und Lieferung Der Anlage War Unser Unternehmen, In Zusammenarbeit Mit Weiteren Mittelständigen Firmen.</p><div class="read"><span>Weiter Lesen</span><span>→</span></div></div></article>
  <article class="ncard" style="left:703px"><div class="img" role="img" aria-label="Braune Glasflaschen auf einer Abfüllanlage"></div><div class="body"><div class="date">März 14, 2024</div><h4>Neue Abfüllanlage für Brunnhof Limo</h4><p>Der Traditionsreiche Limonadenhersteller Brunnhof Limo Aus Der Oberlausitz Investierte 2022/23 In Eine Neue Abfüllanlage. Federführend Beteiligt Bei Planung, Schnittstellenklärung Und Lieferung Der Anlage War Unser Unternehmen, In Zusammenarbeit Mit Weiteren Mittelständigen Firmen.</p><div class="read"><span>Weiter Lesen</span><span>→</span></div></div></article>
  <article class="ncard" style="left:1015px"><div class="img" role="img" aria-label="Braune Glasflaschen auf einer Abfüllanlage"></div><div class="body"><div class="date">März 14, 2024</div><h4>Neue Abfüllanlage für Brunnhof Limo</h4><p>Der Traditionsreiche Limonadenhersteller Brunnhof Limo Aus Der Oberlausitz Investierte 2022/23 In Eine Neue Abfüllanlage. Federführend Beteiligt Bei Planung, Schnittstellenklärung Und Lieferung Der Anlage War Unser Unternehmen, In Zusammenarbeit Mit Weiteren Mittelständigen Firmen.</p><div class="read"><span>Weiter Lesen</span><span>→</span></div></div></article>
</section>

<section class="jobs">
  <div class="person" role="img" aria-label="Ingenieur mit weißem Schutzhelm und verschränkten Armen"></div>
  <h2 class="section-title"><span>JOBS / KARRIERE</span></h2>
  <article class="jcard" style="left:146px"><div class="date">März 14, 2024</div><h4>SPS-Programmierung</h4><p>Lorem Ipsum Dolor Sit Amet, Consectetur Adipiscing Elit, Sed Do Eiusmod Tempor Incididunt Ut Labore Et Dolore Magna Aliqua. Ut Enim Ad Minim Veniam, Quis Nostrud Exercitation Ullamco Laboris Nisi Ut Aliquip Ex Ea Commodo Consequat.</p><span class="apply">Bewerben</span></article>
  <article class="jcard" style="left:459px"><div class="date">März 14, 2024</div><h4>SPS-Programmierung</h4><p>Lorem Ipsum Dolor Sit Amet, Consectetur Adipiscing Elit, Sed Do Eiusmod Tempor Incididunt Ut Labore Et Dolore Magna Aliqua. Ut Enim Ad Minim Veniam, Quis Nostrud Exercitation Ullamco Laboris Nisi Ut Aliquip Ex Ea Commodo Consequat.</p><span class="apply orange">Bewerben</span></article>
  <article class="jcard" style="left:772px"><div class="date">März 14, 2024</div><h4>SPS-Programmierung</h4><p>Lorem Ipsum Dolor Sit Amet, Consectetur Adipiscing Elit, Sed Do Eiusmod Tempor Incididunt Ut Labore Et Dolore Magna Aliqua. Ut Enim Ad Minim Veniam, Quis Nostrud Exercitation Ullamco Laboris Nisi Ut Aliquip Ex Ea Commodo Consequat.</p><span class="apply">Bewerben</span></article>
</section>

<section class="company">
  <h2 class="section-title"><span>UNTERNEHMEN</span></h2>
  <div class="timeline"></div>
  <svg class="pin" style="left:203px" viewBox="0 0 22 45"><line x1="11" y1="11" x2="11" y2="45" stroke="#6ab42d" stroke-width="2"/><circle cx="11" cy="11" r="10" fill="#6ab42d" fill-opacity=".5"/><circle cx="11" cy="11" r="6" fill="#6ab42d"/></svg>
  <svg class="pin" style="left:434px" viewBox="0 0 22 45"><line x1="11" y1="11" x2="11" y2="45" stroke="#6ab42d" stroke-width="2"/><circle cx="11" cy="11" r="10" fill="#6ab42d" fill-opacity=".5"/><circle cx="11" cy="11" r="6" fill="#6ab42d"/></svg>
  <svg class="pin" style="left:665px" viewBox="0 0 22 45"><line x1="11" y1="11" x2="11" y2="45" stroke="#6ab42d" stroke-width="2"/><circle cx="11" cy="11" r="10" fill="#6ab42d" fill-opacity=".5"/><circle cx="11" cy="11" r="6" fill="#6ab42d"/></svg>
  <svg class="pin" style="left:897px" viewBox="0 0 22 45"><line x1="11" y1="11" x2="11" y2="45" stroke="#6ab42d" stroke-width="2"/><circle cx="11" cy="11" r="10" fill="#6ab42d" fill-opacity=".5"/><circle cx="11" cy="11" r="6" fill="#6ab42d"/></svg>
  <svg class="pin" style="left:1128px" viewBox="0 0 22 45"><line x1="11" y1="11" x2="11" y2="45" stroke="#6ab42d" stroke-width="2"/><circle cx="11" cy="11" r="10" fill="#6ab42d" fill-opacity=".5"/><circle cx="11" cy="11" r="6" fill="#6ab42d"/></svg>
  <div class="tcard" style="left:114px"><div class="year">1862</div><h5>Gründung als FG Halden</h5></div>
  <div class="tcard" style="left:345px"><div class="year">1. Weltkrieg</div><h5>Manuelle<br>Blechbearbeitung</h5></div>
  <div class="tcard" style="left:576px"><div class="year">1889</div><h5>Medaillen auf der Weltausstellung in Adelaide</h5></div>
  <div class="tcard" style="left:808px"><div class="year">Nach dem 1. Weltkrieg</div><h5>Wandel zu industriellen Blechbearbeitung</h5></div>
  <div class="tcard" style="left:1039px"><div class="year">1972</div><h5>Verstaatlichung</h5></div>
  <div class="logo"><span class="dot"></span><div><div class="name">KOLMATECH</div><div class="sub">Maschinenbau GmbH</div></div></div>
  <div class="text">
    <p>Das Traditionsreiche Familienunternehmen Kolmatech Plant, Entwickelt Und Baut Pack- Und Palettieranlagen Für Den Getränke- Und Lebensmittelbereich. Mit Erfahrung Und Know-How Planen Und Konstruieren Wir Moderne Und Effiziente Anlagen, Die Optimal Auf Die Bedürfnisse Unserer Kunden Abgestimmt Sind.</p>
    <p>Wir Bieten Ihnen Individuelle Maschinen Und Anlagen Zur Abfüllung Und Verpackung, Sortier- Und Umpackanlagen Sowie Einen Umfassenden Rundum-Service An. Mit Unseren Weltläufigen Produktionsstätten Sind Wir In Der Lage, Die Vorarbeiten Der Montage Unter Unserem Dach Zu Erledigen, Sodass Der Zeitaufwand Für Den Aufbau Bei Ihnen Vor Ort Gering Ist.</p>
    <p>Die Wartung Der Anlagen Und Ein Ersatzteil-Service Sowie Professionelle Unterstützung Und Hilfestellung Bei Problemen Sind Für Uns Selbstverständliche Dienstleistungen.</p>
  </div>
  <span class="btn-dark">Mehr Erfahren</span>
</section>

<section class="contact">
  <h2 class="section-title"><span>KONTAKT</span></h2>
  <form class="form">
    <div class="row"><div><label>Vorname</label><div class="field">Deine Vorname</div></div><div><label>Nachname</label><div class="field">Deine Nachname</div></div></div>
    <div class="row"><div><label>Email</label><div class="field filled">info@kolmatech.de</div></div><div><label>Telefonnummer</label><div class="field">Dein Telefonnummer</div></div></div>
    <div class="area">Schreibe deine Nachricht...</div>
    <div class="send"><svg width="15" height="14" viewBox="0 0 24 22"><path fill="#fff" d="M23 1 1 10l8 3 2 8 4-6 6 4z"/></svg>Senden</div>
  </form>
  <div class="building" role="img" aria-label="Modernes Firmengebäude mit Glasfassade"></div>
</section>

<footer class="footer">
  <div class="fcol" style="left:69px"><h6>KONTAKT</h6>
    <div style="display:flex;gap:38px;margin-top:14px"><div>KOLMATECH Maschinenbau GmbH<br>Am Werkhof 12<br>01234 Talheim</div><div style="line-height:2.25;margin-top:-3px">03541 / 720 - 0<br>03541 / 720 - 14<br>info@kolmatech.de</div></div></div>
  <div class="fcol" style="left:359px"><h6>QUICKLINKS</h6>
    <div class="links" style="grid-template-columns:auto auto auto"><span>Unternehmen</span><span>Packertechnik</span><span>Gebrauchtmaschinen</span><span>Jobs / Karriere</span><span>Fördertechnik</span><span>Aktuelles</span><span>Palettiertechnik</span><span>Anlagen</span></div></div>
  <div class="fcol" style="left:676px"><h6>PRODUKTE</h6>
    <div class="links" style="grid-template-columns:auto auto"><span>PALETTIERTECHNIK</span><span>FÖRDERTECHNIK</span><span>PACKERTECHNIK</span><span>GEBRAUCHTMASCHINEN</span></div></div>
  <div class="newsletter"><div class="lbl">Abonnieren Sie den Newsletter</div>
    <div class="box"><div class="in">Email</div><div class="go"><svg width="11" height="10" viewBox="0 0 12 10"><path d="M0 5h10M6 1l4 4-4 4" stroke="#fff" stroke-width="2" fill="none"/></svg></div></div></div>
  <div class="copy">©2024. Kolmatech All rights reserved</div>
</footer>

</body>
</html>
```